TALVORNE End User Instruction Guide

I need to create a 5 to 7-page instruction guides for customers who purchased a phone system from our company. The document is a quick reference guide that will help end-users learn how to set up and use their new desk phone and software applications. I need the guide to be 3 x 5 or 6 x 8 in size and will fold like a book.

Target Market(s)

Business users / Quorblen Desk Phone Users / TalVORNE Portal users

Industry/Entity Type

Telecommunications

Font styles to use
Serif

Colors
0758a5
ffffff

Requirements
Must have
• Need to have step-by-step instructions that include the information from the QuickStart guide I provided. I need to see an image of the phone with an arrow pointing to the key on the phone that should be pressed. For example, when checking voicemail the Messages key is pressed and I want to highlight this button or call it out somehow.

I need to have three pages for setup instructions, one page for shortcuts or features codes and our support contacts on the last page.
Nice to have
• I want to have a page for notes that the end-user can use during training. I would also like to have a blank space next to passwords and user ID's so they can be filled out with specific details that are provided during their training. For example, in the voicemail section, I include a default PIN. I would like to leave this blank and let the end-user fill it out during training.
Should not have
• Complex shapes and designs. I like straight lines and a simple easy to understand layout.

```html
<!DOCTYPE html>
<html lang="en">
<head>
<meta charset="utf-8">
<title>TALVORNE End User Quick Start Guide</title>
<link rel="stylesheet" href="https://fonts.googleapis.com/css2?family=Montserrat:wght@800&family=Source+Sans+3:wght@400;600;700&display=swap">
<style>
:root{
  --navy:#22387e;
  --blue:#2e4b9b;
  --ink:#444446;
  --footer:#3a3a3c;
  --backdrop:#cfcfd1;
  --rule:#6b6b6d;
}
*{box-sizing:border-box;margin:0;padding:0}
html,body{width:1200px;height:2476px;overflow:hidden}
body{background:linear-gradient(180deg,#d6d6d8,#c8c8ca);font-family:"Source Sans 3",Arial,sans-serif;color:var(--ink);position:relative}
.spread{position:absolute;left:198px;width:832px;height:546px;display:flex;box-shadow:0 4px 10px rgba(0,0,0,.25)}
.spread.cover-spread{height:554px}
.page{position:relative;width:416px;height:100%;overflow:hidden}
.page.left{background:linear-gradient(90deg,#fff 78%,#ebebec 100%)}
.page.right{background:linear-gradient(90deg,#e3e3e5 0%,#fff 14%)}
.abs{position:absolute}

/* brand */
.brand{position:absolute;display:flex;align-items:center;gap:6px;color:var(--navy);font-weight:700;letter-spacing:.5px}
.brand .mark{background:var(--navy);display:block}
.inner .brand{left:28px;top:23px;font-size:19px}
.inner .brand .mark{width:15px;height:15px}
.guide-band{position:absolute;left:200px;top:34px;width:198px;height:19px;background:var(--navy);color:#fff;font-weight:700;font-size:10.5px;line-height:19px;text-align:center;clip-path:polygon(14px 0,100% 0,100% 100%,0 100%)}
.band-rule{position:absolute;left:176px;top:52px;width:30px;height:1px;background:var(--navy)}
.page-foot{position:absolute;left:0;right:0;bottom:0;height:17px;background:var(--footer);color:#fff;font-size:7px;font-weight:600;line-height:17px;text-align:right;padding-right:20px}

/* type */
.h-step{font-size:14px;color:var(--blue);font-weight:400}
.h-step b{font-weight:700}
.h-caps{font-size:13px;color:var(--blue);font-weight:700;letter-spacing:.2px}
.h-sub{font-size:10px;color:var(--blue);font-weight:700}
.h-mini{font-size:8.2px;color:#333;font-weight:700}
.p{font-size:8px;line-height:1.38;text-align:justify;color:var(--ink)}
.p b{color:#333}
.list{list-style:none;font-size:8px;line-height:1.45;color:var(--ink)}
.list li{position:relative;padding-left:8px}
.list li::before{content:"•";position:absolute;left:0}
.dots{list-style:none;font-size:8px;line-height:1.4;color:var(--ink)}
.dots li{position:relative;padding-left:15px}
.dots li::before{content:"";position:absolute;left:0;top:3px;width:6px;height:6px;border-radius:50%;background:var(--blue)}
.dots li b{color:#333}
.key{display:inline-block;width:10px;height:10px;background:#2c2c2e;border-radius:2px;vertical-align:-2px;color:#fff;font-size:7px;line-height:10px;text-align:center;font-weight:700}
.key.light{background:#fff;border:1px solid #333}
.fill{display:inline-block;border-bottom:1px solid #777;vertical-align:baseline}

/* cover */
.cover .title{position:absolute;left:22px;top:44px;font-family:Montserrat,Arial,sans-serif;font-weight:800;font-size:32px;line-height:41px;color:#fff;letter-spacing:.3px}
.cover .brand{left:66px;top:452px;font-size:36px;gap:10px}
.cover .brand .mark{width:30px;height:30px}
.contact-bar{position:absolute;left:0;right:0;bottom:0;height:40px;background:var(--navy);color:#fff;font-size:7.2px;display:flex;align-items:center;justify-content:space-around;padding:0 8px}
.contact-bar span{display:flex;align-items:center;gap:4px}
.contact-bar svg{width:9px;height:9px}

/* star codes */
.codes-title{left:21px;top:48px;font-size:8.5px;color:var(--navy);font-weight:700}
.concept{top:66px;width:182px;font-size:5.6px;line-height:1.3;text-align:justify}
.concept b{color:var(--navy);display:block;font-size:6px}
.codes{position:absolute;left:21px;top:124px;width:379px;height:368px;border:1px solid var(--rule);border-collapse:collapse;table-layout:fixed;font-size:4.7px;color:#333}
.codes th{height:13px;background:#ececee;font-size:5.4px;text-align:left;padding-left:3px;border-bottom:1px solid var(--rule)}
.codes td{height:11px;padding:0 3px;vertical-align:top;line-height:1.2;overflow:hidden;white-space:nowrap}
.codes .sep{border-right:1px solid var(--rule)}
.codes tr.pad td{height:auto}

.shot{position:absolute;border-radius:3px}
</style>
</head>
<body>

<!-- Spread 1: star codes + cover -->
<section class="spread cover-spread" style="top:114px">
  <div class="page left">
    <h2 class="abs codes-title">STAR CODES AND FEATURES</h2>
    <p class="abs concept" style="left:21px"><b>Concept</b>Many features in the HubCentral platform are controlled by dialing the star key in conjunction with a 2 or 3 digit code. The default star codes are listed below. These may be customized per domain by the Cloudmere AdminDesk.</p>
    <p class="abs concept" style="left:210px;width:190px"><b>Reserved Number Space</b>Certain 3–4 digit extensions should NOT be used. Please be aware of the Reserved Number Space page to avoid any conflicts with dial translations.</p>
    <table class="codes">
      <colgroup><col style="width:41px"><col style="width:147px"><col style="width:43px"><col></colgroup>
      <tr><th>STAR CODE</th><th class="sep">FEATURE DESCRIPTION</th><th>STAR CODE</th><th>FEATURE DESCRIPTION</th></tr>
      <tr><td>***</td><td class="sep">Dynamically park a call (701–709 range)</td><td>*74</td><td>Activate night mode (requires setup)</td></tr>
      <tr><td>*(lot)</td><td class="sep">Park a call to a specified park slot</td><td>*75</td><td>Deactivate night mode</td></tr>
      <tr><td>*55(ext)</td><td class="sep">Extension pickup – answer a ringing call</td><td>*78</td><td>Activate do not disturb</td></tr>
      <tr><td>*56</td><td class="sep">Domain pickup – answer any call in domain</td><td>*79</td><td>Deactivate do not disturb</td></tr>
      <tr><td>*57</td><td class="sep">Department pickup – answer in department</td><td>*80</td><td>Start call recording</td></tr>
      <tr><td>*58</td><td class="sep">Self pickup – move call to another phone</td><td>*81</td><td>Stop call recording</td></tr>
      <tr><td>*40</td><td class="sep">Activate call forwarding</td><td>*82</td><td>Pause recording for 1 minute or until *83</td></tr>
      <tr><td>*41</td><td class="sep">Set forward busy destination</td><td>*83</td><td>Resume call recording from pause</td></tr>
      <tr><td>*42</td><td class="sep">Set forward no answer feature</td><td>*88</td><td>Make agent available for all queues</td></tr>
      <tr><td>*44</td><td class="sep">Hotdesking login – needs user and password</td><td>*89</td><td>Make agent unavailable for all queues</td></tr>
      <tr><td>*45</td><td class="sep">Disable call forwarding (deprecated)</td><td>*90</td><td>Activate forward busy</td></tr>
      <tr><td>*46</td><td class="sep">Hotdesking logout – needs current password</td><td>*91</td><td>Deactivate forward busy</td></tr>
      <tr><td>*48</td><td class="sep">Ask caller for PIN before connecting</td><td>*92</td><td>Activate forward no answer</td></tr>
      <tr><td>*49</td><td class="sep">Ask caller for extension before connecting</td><td>*93</td><td>Deactivate forward no answer</td></tr>
      <tr><td>*50(ext)</td><td class="sep">Auto answer intercom (3 or 4 digit ext)</td><td>*97(ext)</td><td>Transfer to a 4-digit extension</td></tr>
      <tr><td>*55(lot)</td><td class="sep">Retrieve a call from a call park queue</td><td>*98(ext)</td><td>Transfer to a 3-digit extension</td></tr>
      <tr><td>*61</td><td class="sep">To voicemail – unauthenticated</td><td>*99</td><td>Transfer to self</td></tr>
      <tr><td>*62</td><td class="sep">To voicemail – password only</td><td>Shortcut</td><td>Feature description</td></tr>
      <tr><td>*66&lt;10/11</td><td class="sep">Digit number &gt; route call off-net</td><td>7(ext)</td><td>Transfer a call directly to voicemail</td></tr>
      <tr><td>*67&lt;10/11</td><td class="sep">Digit number &gt; connect with privacy</td><td>71(0-9)</td><td>Transfer to park queue 710–719</td></tr>
      <tr><td>*67(ext)</td><td class="sep">To user with privacy</td><td>72(0-9)</td><td>Transfer to park queue 720–729</td></tr>
      <tr><td>*69</td><td class="sep">Call return</td><td>99(ext)</td><td>Auto answer intercom, not with SLA</td></tr>
      <tr><td>*72&lt;10/11</td><td class="sep">Digit number &gt; set forward destination</td><td>099</td><td>Invoke the account code feature</td></tr>
      <tr><td>*73</td><td class="sep">Deactivate forward</td><td>5000</td><td>Unregistered login to voicemail</td></tr>
      <tr><td></td><td class="sep"></td><td>5001</td><td>Registered login to voicemail</td></tr>
      <tr><td></td><td class="sep"></td><td>5002</td><td>Hot desking sign in</td></tr>
      <tr><td></td><td class="sep"></td><td>5003</td><td>Request PIN, then 2nd dial tone</td></tr>
      <tr class="pad"><td></td><td class="sep"></td><td></td><td></td></tr>
    </table>
    <div class="contact-bar">
      <span><svg viewBox="0 0 10 10"><circle cx="5" cy="5" r="5" fill="#fff"/><rect x="2.5" y="3.3" width="5" height="3.4" fill="var(--navy)"/></svg>support@talvornecommunications.com</span>
      <span><svg viewBox="0 0 10 10"><path d="M2 1l2 2-1 1.5c.7 1.3 1.5 2.1 2.6 2.6L7 6l2 2-1.5 1.5C4.5 9 1 5.5.5 2.5z" fill="#fff"/></svg>555-010-4420</span>
      <span><svg viewBox="0 0 10 10"><circle cx="5" cy="5" r="4.3" fill="none" stroke="#fff" stroke-width="1.2"/><circle cx="5" cy="5" r="1.6" fill="#fff"/></svg>www.talvornecommunications.com</span>
    </div>
  </div>

  <div class="page right cover" style="background:#fff">
    <svg class="abs" style="left:0;top:0" width="416" height="514" viewBox="0 0 416 514">
      <defs>
        <linearGradient id="officeTone" x1="0" y1="0" x2="1" y2="1">
          <stop offset="0" stop-color="#c9ced6"/><stop offset=".55" stop-color="#8f97a4"/><stop offset="1" stop-color="#4d5563"/>
        </linearGradient>
        <linearGradient id="deskPhoneTone" x1="0" y1="0" x2="1" y2="1">
          <stop offset="0" stop-color="#55585d"/><stop offset="1" stop-color="#1f2023"/>
        </linearGradient>
      </defs>
      <polygon points="300,0 416,0 416,240 290,356 0,356 0,300" fill="url(#officeTone)" role="img" aria-label="Photo of a business team meeting in a bright office"/>
      <polygon points="0,0 300,0 362,62 108,316 0,316" fill="var(--navy)"/>
      <rect x="210" y="266" width="190" height="150" rx="10" fill="url(#deskPhoneTone)" role="img" aria-label="Photo of a Quorblen touchscreen desk phone"/>
    </svg>
    <h1 class="title">END USER<br>QUICK START<br>GUIDE</h1>
    <div class="brand"><span class="mark"></span>TALVORNE</div>
    <div class="contact-bar">
      <span><svg viewBox="0 0 10 10"><circle cx="5" cy="5" r="5" fill="#fff"/><rect x="2.5" y="3.3" width="5" height="3.4" fill="var(--navy)"/></svg>support@talvornecommunications.com</span>
      <span><svg viewBox="0 0 10 10"><path d="M2 1l2 2-1 1.5c.7 1.3 1.5 2.1 2.6 2.6L7 6l2 2-1.5 1.5C4.5 9 1 5.5.5 2.5z" fill="#fff"/></svg>555-010-4420</span>
      <span><svg viewBox="0 0 10 10"><circle cx="5" cy="5" r="4.3" fill="none" stroke="#fff" stroke-width="1.2"/><circle cx="5" cy="5" r="1.6" fill="#fff"/></svg>www.talvornecommunications.com</span>
    </div>
  </div>
</section>

<!-- Spread 2: voicemail -->
<section class="spread" style="top:709px">
  <div class="page left inner">
    <div class="brand"><span class="mark"></span>TALVORNE</div>
    <div class="band-rule"></div><div class="guide-band">END-USER QUICK START GUIDE</div>

    <h2 class="abs h-step" style="left:21px;top:82px"><b>STEP 1:</b> Set-Up Your Voicemail</h2>
    <p class="abs p" style="left:21px;right:18px;top:112px">The first time you log in to your mailbox, you are walked through recording your name for the directory and recording your personal greeting. The name recording is for the dial-by-name directory, so when someone enters the first three letters of your last name, it will playback your name recording. The greeting plays when your mailbox is reached. It is essential to make a custom message, as many callers will not leave messages at mailboxes that have generic greetings.</p>

    <h3 class="abs h-sub" style="left:21px;top:218px">Accessing Voicemail from your Desk Phone</h3>
    <ul class="abs dots" style="left:21px;right:18px;top:240px">
      <li>Press the <b>Messages</b> <span class="key light"></span> button on your phone to access your voicemail box, or dial 5001 if you can not identify the voicemail button.</li>
      <li style="margin-top:12px">When prompted, enter your default voicemail pin <span class="fill" style="width:34px"></span>, and then press <span class="key">#</span></li>
    </ul>
    <p class="abs p" style="left:36px;right:14px;top:298px"><b>Note:</b> If you subscribe to multiple mailboxes, press the left or right arrows on the directional pad to select the extension of the voicemail you want to access. Then follow the steps above.</p>

    <h3 class="abs h-sub" style="left:21px;top:364px">To access another person’s mailbox</h3>
    <ul class="abs dots" style="left:21px;right:18px;top:386px">
      <li>Dial <b>5000</b>.</li>
      <li>When prompted, enter the other person’s extension number.</li>
      <li>Enter the voicemail PIN of the other person’s mailbox, followed by <b>#</b>.</li>
    </ul>
    <div class="page-foot">www.talvornecommunications.com</div>
  </div>

  <div class="page right inner">
    <div class="brand"><span class="mark"></span>TALVORNE</div>
    <div class="band-rule"></div><div class="guide-band">END-USER QUICK START GUIDE</div>

    <h3 class="abs h-sub" style="left:21px;top:84px">Accessing Voicemail from the user portal</h3>
    <ul class="abs list" style="left:21px;top:104px">
      <li>Start a web browser.</li>
      <li>Go to <b>phone.talvornecommunications.com</b></li>
    </ul>
    <div class="shot" style="left:18px;top:146px;width:92px;height:104px;background:linear-gradient(180deg,#f6f7f9,#e4e7ec);box-shadow:0 1px 3px rgba(0,0,0,.25)" role="img" aria-label="Screenshot of the portal login form"></div>
    <p class="abs p" style="left:124px;right:16px;top:168px;text-align:left">Click in the Login name field and type your user name<br><span class="fill" style="width:170px"></span>(ext@customerdomain).</p>
    <p class="abs p" style="left:124px;right:14px;top:202px;text-align:left">Your customerdomain typically is the same as your email address domain. Click in the Password field and enter your user password.<br>(default password is <span class="fill" style="width:128px"></span></p>

    <div class="shot" style="left:22px;top:270px;width:372px;height:142px;background:linear-gradient(180deg,#eef0f3 0%,#f7f8fa 30%,#fafbfc 100%)" role="img" aria-label="Screenshot of the portal toolbar and Messages page listing voicemails"></div>

    <h3 class="abs h-sub" style="left:21px;top:424px">Record your greeting</h3>
    <ul class="abs list" style="left:21px;right:18px;top:444px">
      <li>From the <b>Settings</b> tab of the Messages page, click the speaker icon <span class="key">&#9664;</span></li>
      <li>Next to <b>New Greeting</b>, click <b>Record</b> and the system will call you, or upload an existing greeting.</li>
    </ul>
    <div class="page-foot">www.talvornecommunications.com</div>
  </div>
</section>

<!-- Spread 3: mobile app + desk phone -->
<section class="spread" style="top:1307px">
  <div class="page left inner">
    <div class="brand"><span class="mark"></span>TALVORNE</div>
    <div class="band-rule"></div><div class="guide-band">END-USER QUICK START GUIDE</div>

    <h2 class="abs h-step" style="left:21px;top:82px"><b>STEP 2:</b> Setting up the mobile application</h2>
    <h3 class="abs h-sub" style="left:21px;top:117px">Installing Mobile Application</h3>
    <div class="abs" style="left:21px;top:145px;width:114px;height:108px;background:#f1f1f2">
      <div style="height:22px;background:#b9b9bb;color:#fff;font-size:10px;font-weight:600;line-height:22px;text-align:center">Get the app</div>
      <div style="margin:16px 0 0 20px;width:74px;height:24px;background:#111;border-radius:4px"></div>
      <div style="margin:12px 0 0 20px;width:74px;height:24px;background:#111;border-radius:4px"></div>
    </div>
    <p class="abs" style="left:21px;top:265px;font-size:8px;font-weight:700;color:var(--blue)">Search LinkRelay and click install</p>
    <div class="abs" style="left:158px;top:256px;width:24px;height:24px;border-radius:5px;background:#5b86b8"></div>

    <div class="shot" style="left:22px;top:303px;width:92px;height:214px;border-radius:12px;background:linear-gradient(180deg,#e9e9eb 0 6%,#2a2a2d 6% 92%,#e9e9eb 92%);box-shadow:0 1px 3px rgba(0,0,0,.3)" role="img" aria-label="Mobile app in-call screen"></div>
    <div class="shot" style="left:120px;top:303px;width:94px;height:214px;border-radius:12px;background:linear-gradient(180deg,#ececee 0 6%,#fafafa 6% 92%,#ececee 92%);box-shadow:0 1px 3px rgba(0,0,0,.3)" role="img" aria-label="Mobile app sign-in screen"></div>

    <h3 class="abs" style="left:232px;top:364px;font-size:8.5px;font-weight:700;color:var(--blue)">Zero Touch Configuration</h3>
    <p class="abs p" style="left:232px;right:18px;top:380px">To use LinkRelay simply log-in with the credential from your PBX portal. That’s all there is to it. All the features that you are accustomed to will pre-configured and ready for you.</p>
    <div class="page-foot">www.talvornecommunications.com</div>
  </div>

  <div class="page right inner">
    <div class="brand"><span class="mark"></span>TALVORNE</div>
    <div class="band-rule"></div><div class="guide-band">END-USER QUICK START GUIDE</div>

    <h2 class="abs h-step" style="left:19px;top:82px"><b>STEP 3:</b> Using your desk phone</h2>
    <h3 class="abs h-sub" style="left:21px;top:119px">Making Calls</h3>
    <p class="abs" style="left:21px;right:20px;top:139px;font-size:8px;font-weight:600;line-height:1.4;color:#333">Making a call with your phone does not require a leading 9. You can dial on-hook or off-hook.</p>
    <ul class="abs dots" style="left:21px;top:175px"><li><b>To dial on-hook</b></li></ul>
    <ul class="abs list" style="left:21px;top:189px"><li>Dial the phone number.</li><li>Pick up the handset, headset, or speaker.</li></ul>
    <ul class="abs dots" style="left:21px;top:230px"><li><b>To dial off-hook</b></li></ul>
    <ul class="abs list" style="left:21px;top:244px"><li>Pick up the handset, headset, or speaker.</li><li>Dial the phone number.</li><li>Calls to the US and Canada are all dialed using 10 or 11 digits.</li></ul>

    <h3 class="abs h-sub" style="left:21px;top:314px">Receiving Calls</h3>
    <p class="abs" style="left:21px;right:14px;top:333px;font-size:8px;font-weight:600;color:#333">When a call comes in, you can answer it via a headset, speakerphone, or handset.</p>
    <ul class="abs dots" style="left:21px;right:20px;top:349px">
      <li><b>To answer a call using a handset</b><br>– Lift the handset off-hook.</li>
      <li style="margin-top:4px"><b>To answer a call using a speakerphone</b><br>– Press the Speaker button.</li>
      <li style="margin-top:4px"><b>To answer a call using a headset</b><br>Usage depends on how the headset is connected. Often, you’ll press the button on the headset or press the headset button on the phone.</li>
    </ul>
    <div class="page-foot">www.talvornecommunications.com</div>
  </div>
</section>

<!-- Spread 4: handling calls -->
<section class="spread" style="top:1914px">
  <div class="page left inner">
    <div class="brand"><span class="mark"></span>TALVORNE</div>
    <div class="band-rule"></div><div class="guide-band">END-USER QUICK START GUIDE</div>

    <h2 class="abs h-caps" style="left:21px;top:83px">HANDLING CALLS</h2>
    <p class="abs p" style="left:21px;right:18px;top:104px">Your cloud PBX features various ways to move calls around, including attended transfer, unattended (blind) transfer, voicemail transfer, park, and more. In this section, references to BLFs are the 1-touch buttons to extensions common at front-desk phones.</p>

    <h3 class="abs h-sub" style="left:21px;top:169px">Attended Transfer</h3>
    <p class="abs p" style="left:21px;right:18px;top:187px">Attended transfer allows you to speak to the transfer recipient prior to completing the transfer while the caller is on hold.</p>
    <p class="abs h-mini" style="left:21px;top:227px">To perform an attended transfer using Vantrel and Quorblen phones</p>
    <ul class="abs list" style="left:21px;right:18px;top:243px">
      <li>Press the <b>Transfer key/softkey</b> <span class="key">&#8644;</span> on your phone.</li>
      <li>Dial the recipient’s extension or press their <b>BLF</b>.</li>
      <li>Speak to the recipient, and then either press <b>Transfer</b> <span class="key">&#8644;</span> again to complete or cancel if the recipient cannot take the call.</li>
    </ul>

    <h3 class="abs h-sub" style="left:21px;top:317px">Blind Transfer</h3>
    <p class="abs h-mini" style="left:21px;top:331px">To blind transfer using Quorblen phones</p>
    <ul class="abs list" style="left:21px;top:347px">
      <li>Press <b>Transfer</b> <span class="key">&#8644;</span></li>
      <li>Dial the extension of the recipient.</li>
      <li>Press <b>Transfer</b> <span class="key">&#8644;</span></li>
    </ul>
    <div class="page-foot">www.talvornecommunications.com</div>
  </div>

  <div class="page right inner">
    <div class="brand"><span class="mark"></span>TALVORNE</div>
    <div class="band-rule"></div><div class="guide-band">END-USER QUICK START GUIDE</div>

    <h3 class="abs h-sub" style="left:23px;top:86px">Transfers to External Numbers</h3>
    <p class="abs p" style="left:23px;right:18px;top:105px">A transfer can also go to an external number such as a cell phone. Follow the transfer directions above but instead of dialing an extension, dial a 10-digit phone number.</p>

    <h3 class="abs h-sub" style="left:21px;top:146px">Park and Hold</h3>
    <p class="abs p" style="left:19px;right:18px;top:164px">On your phone system, hold is a local function. This means a call held on your phone cannot be picked up at another station. Park is a system-wide function. This means a call parked at one phone may be picked up by any phone.</p>

    <p class="abs h-mini" style="left:21px;top:213px">To park a call</p>
    <ul class="abs list" style="left:21px;right:18px;top:231px">
      <li>Dial *** in an active call from any phone. The system says, “The call is parked at 7xx.”</li>
      <li>Hang up.</li>
      <li>To retrieve the parked call, dial <b>7xx</b> where xx is the number stated by the system.</li>
    </ul>

    <h2 class="abs h-caps" style="left:20px;top:318px">EMERGENCY 911 CALLS</h2>
    <ul class="abs list" style="left:21px;right:18px;top:340px">
      <li>When you dial 911 from LinkRelay running on a mobile phone, the application will automatically dial out using your existing cellular service. 911 calls from your mobile phone will not be routed through your UCaaS service provider.</li>
      <li style="margin-top:9px">911 calls dialed from the desktop (WebRTC) app will be routed through your UCaaS service provider (the same as any other softphone).</li>
    </ul>
    <div class="page-foot">www.talvornecommunications.com</div>
  </div>
</section>

</body>
</html>
```